Create an awesome website for a medical clinic

This is a new website for a doctor's office. The site should be clean and modern, easy to navigate.

This is a wellness clinic, we want to help our clients have a healthy, active lifestyle. It should be friendly and inviting, and easy for them to call or schedule an appointment.

The site should be responsive and designed using the attached Bootstrap 3 PSD.

We will provide stock photos, until then please use stock photos from:

pixelharbor.com or
framequarry.com (preferred)

Some example sites of clean and modern designs that we like:

https://tulsaspinecare.com/
http://reachpastjoints.com/
http://turninghealthier.com/

Also attached is a temporary logo you can use.

Reason: Thank you everyone for your great designs - we need a little more time so I'm extending the project.

Need extra days to review

Also, the colors in the new logo I just linked to are the final colors of the logo, so feel free to use any complimentary colors to it.

Hi everyone, The boss wants to change the layout of the site a little bit - here's the revised layout: https://www.filecrate.com/s/k9rt31vx2qp84zn/notes%2011_29_2017.pdf?dl=0 And the graphic assets you can use are here: https://www.filecrate.com/s/k9rt31vx2qp84zn/notes%2011_29_2017.pdf?dl=0 Feel free to change the background color of the "topbar", and change the icons of the "why people trust us" if you want, these are just temporary placeholders. Thanks for your patience and hard work!

Target Market(s)

People seeking medical treatment (wellness clinic)

Industry/Entity Type

Doctor

Number of Pages Required

1 page

Font styles to use
Sans Serif

Colors
0592cd
33a6d7
abd037
9bcb3c

Requirements
Must have
• The home page should have: a strong hero image/slideshow, clinic phone number should be prominent and at the top of the page (in the nav), a "what to expect" section (this is like a FAQs section - see attachment), and a strong call to action (a button to call or schedule an appointment).
• The what to expect section is useful so that prospective clients can determine if we're a good fit for them or not. It's a basic, first-step pre-qualification block of information.
• Social media icons which links to our social media profiles should be included.
Nice to have
• - Link to 3 most recent blog entries
• - Testimonials
• - How a multilevel nav menu looks.

```html
<!DOCTYPE html>
<html lang="en">
<head>
<meta charset="utf-8">
<title>Willowmere Health Clinic</title>
<link href="https://fonts.googleapis.com/css2?family=Roboto:wght@300;400;500;700;900&display=swap" rel="stylesheet">
<style>
:root{
  --blue:#0592cd;
  --blue-light:#33a6d7;
  --blue-dark:#0a6f9f;
  --green:#9bcb3c;
  --green-bright:#abd037;
  --green-deep:#6fae2c;
  --ink:#333b44;
  --muted:#6b7580;
  --line:#e3e8ec;
  --white:#ffffff;
}
*{box-sizing:border-box;margin:0;padding:0}
html,body{width:1200px;height:3240px;overflow:hidden}
body{font-family:"Roboto",Arial,sans-serif;color:var(--ink);background:var(--white);font-size:14px;line-height:1.6}
.wrap{width:976px;margin:0 auto;position:relative;height:100%}
.btn{display:inline-block;background:var(--green);color:var(--white);font-weight:500;font-size:14px;letter-spacing:.5px;text-transform:uppercase;padding:11px 26px;border-radius:2px}
.btn-dark{background:var(--blue-dark)}
.btn-white{background:var(--white);color:var(--blue)}
.ph{display:block}

/* header */
.site-header{height:120px}
.site-header .wrap{display:flex;align-items:center;justify-content:space-between}
.brand{color:var(--green);font-weight:900;line-height:1;text-transform:uppercase}
.brand .b1{font-size:44px;display:block}
.brand .b2{font-size:22px;display:block;margin-top:4px}
.header-actions{display:flex;align-items:center;gap:40px}
.call{display:flex;align-items:center;gap:12px}
.call-icon{width:40px;height:40px;border-radius:50%;background:var(--green);display:flex;align-items:center;justify-content:center}
.call small{display:block;font-size:12px;color:var(--muted);letter-spacing:1px}
.call strong{font-size:26px;color:var(--green);font-weight:700;line-height:1}

/* nav */
.main-nav{height:40px;border-top:1px solid var(--line);border-bottom:1px solid var(--line)}
.main-nav ul{list-style:none;display:flex;justify-content:space-between;height:100%;width:976px;margin:0 auto}
.main-nav li{font-size:13px;font-weight:500;text-transform:uppercase;color:var(--muted);display:flex;align-items:center;padding:0 18px}
.main-nav li.active{background:var(--green);color:var(--white)}

/* hero */
.hero{height:440px;position:relative;background:linear-gradient(100deg,#5f8fa8 0%,#9dc1d3 45%,#d8e7ee 70%,#e9f1f5 100%)}
.hero .ph{position:absolute;inset:0}
.hero-text{position:absolute;left:112px;top:130px}
.hero h1{font-size:66px;font-weight:700;color:var(--white);letter-spacing:1px;line-height:1}
.hero p{color:var(--green-bright);font-weight:700;font-size:16px;text-transform:uppercase;margin:14px 0 26px;letter-spacing:.5px}
.arrow{position:absolute;top:200px}
.arrow.l{left:16px}.arrow.r{right:16px}
.dots{position:absolute;left:148px;bottom:22px;display:flex;gap:8px}
.dots i{width:10px;height:10px;border-radius:50%;background:rgba(255,255,255,.5)}
.dots i:first-child{background:var(--white)}

/* about */
.about{height:380px}
.about .wrap{display:flex;gap:44px;padding-top:60px}
.about-photo{width:268px;height:260px;border:6px solid var(--green);background:linear-gradient(135deg,#cfe3ec,#eaf3f6 60%,#b9d4df)}
.about-body{flex:1;padding-top:8px}
.section-title{font-size:30px;font-weight:700;text-transform:uppercase;line-height:1.2}
.section-title .g{color:var(--green)}
.section-title .b{color:var(--blue)}
.about-body p{color:var(--muted);font-size:14px;margin:14px 0 20px}

/* what we do */
.services{height:600px;background:linear-gradient(180deg,var(--blue) 0%,var(--blue-light) 100%);color:var(--white);text-align:center}
.services .section-title{color:var(--white);padding-top:64px}
.rule{width:60px;height:3px;background:var(--green);margin:14px auto 0}
.cards{display:flex;gap:16px;margin-top:56px}
.card{flex:1;height:290px;background:rgba(255,255,255,.16);border:1px solid rgba(255,255,255,.35);padding:26px 20px;display:flex;flex-direction:column;align-items:center}
.card-icon{width:76px;height:76px;border-radius:50%;background:var(--green);border:4px solid rgba(255,255,255,.6);display:flex;align-items:center;justify-content:center}
.card h3{font-size:17px;font-weight:500;margin:18px 0 8px}
.card p{font-size:13px;line-height:1.55;opacity:.9;margin-bottom:auto}
.card .btn{font-size:12px;padding:8px 22px}
.services .view{margin-top:38px}

/* what to expect */
.expect{height:460px}
.expect .wrap{display:flex;gap:30px;padding-top:48px}
.faq{width:330px}
.faq h4{font-size:15px;font-weight:700;margin-top:14px}
.faq p{font-size:13px;color:var(--muted);line-height:1.5}
.faq .btn{margin-top:18px}
.expect-photo{width:270px;height:390px;background:linear-gradient(180deg,#eaf3f7,#cfe1ea 70%,#b5cfdc)}
.hours{flex:1;background:var(--green);color:var(--white);padding:26px 28px;height:370px}
.hours h3{font-size:26px;font-weight:400;text-transform:uppercase;text-align:center;margin-bottom:16px}
.hours table{width:100%;border-collapse:collapse;font-size:14px}
.hours td{padding:9px 0;border-bottom:1px solid rgba(255,255,255,.35)}
.hours td:last-child{text-align:right}
.emergency{margin-top:22px;text-align:center}
.emergency small{font-size:13px;text-transform:uppercase;letter-spacing:1px}
.emergency strong{display:block;background:var(--white);color:var(--green-deep);font-size:26px;font-weight:700;padding:6px 0;margin-top:6px}
.emergency p{font-size:12px;margin-top:10px;line-height:1.4}

/* testimonial */
.testimonial{height:420px;background:linear-gradient(180deg,var(--blue-light),var(--blue));color:var(--white);text-align:center;position:relative}
.testimonial .section-title{color:var(--white);padding-top:56px}
.avatar{width:88px;height:88px;border-radius:50%;background:#d9e6ec;border:4px solid var(--white);margin:30px auto 20px}
.testimonial blockquote{width:800px;margin:0 auto;font-size:15px;line-height:1.6;font-style:italic;opacity:.95}
.testimonial cite{display:block;margin-top:14px;font-style:normal;font-size:14px}
.testimonial cite b{color:var(--green-bright)}
.testimonial .arrow{top:210px}

/* blog */
.blog{height:520px;text-align:center}
.blog .section-title{color:var(--green);padding-top:48px}
.posts{display:flex;gap:26px;margin-top:40px;text-align:left}
.post{flex:1;position:relative}
.post-photo{height:180px}
.p1{background:linear-gradient(135deg,#6aa3c2,#c7dfe9)}
.p2{background:linear-gradient(135deg,#e4c8a8,#a9cde0)}
.p3{background:linear-gradient(135deg,#d9e3e8,#8fb3c6)}
.date{position:absolute;left:14px;top:0;background:var(--blue);color:var(--white);width:48px;text-align:center;font-size:11px;line-height:1.1;padding:6px 0}
.date b{display:block;font-size:20px}
.post-caption{background:var(--blue);color:var(--white);margin:-28px 14px 0;position:relative;padding:14px 16px}
.post-caption h4{font-size:15px;font-weight:500}
.post-caption p{font-size:12px;opacity:.85;line-height:1.45;margin-top:4px}
.post .more{display:inline-block;margin:10px 14px 0;font-size:12px;font-weight:700;color:var(--blue);text-transform:uppercase}
.blog .view{margin-top:34px}

/* footer */
.site-footer{height:260px;background:var(--blue);color:var(--white)}
.site-footer .wrap{display:flex;gap:36px;padding-top:40px}
.foot-brand{width:260px}
.foot-brand .brand{color:var(--white)}
.foot-brand p{font-size:12px;opacity:.85;margin-top:14px;line-height:1.5}
.foot-col{width:180px}
.foot-col h5{font-size:14px;font-weight:700;text-transform:uppercase;margin-bottom:10px}
.foot-col li{list-style:none;font-size:12px;opacity:.9;line-height:1.8}
.foot-contact{flex:1}
.foot-contact li{list-style:none;font-size:12px;line-height:1.8}
.foot-contact li b{font-weight:700;margin-right:6px}
.foot-contact .btn{margin-top:18px;display:block;text-align:center}
</style>
</head>
<body>

<header class="site-header">
  <div class="wrap">
    <div class="brand"><span class="b1">Willowmere</span><span class="b2">Health Clinic</span></div>
    <div class="header-actions">
      <div class="call">
        <span class="call-icon">
          <svg width="20" height="20" viewBox="0 0 24 24"><path fill="#fff" d="M6.6 10.8a15 15 0 0 0 6.6 6.6l2.2-2.2c.3-.3.7-.4 1-.2 1.1.4 2.3.6 3.6.6.6 0 1 .4 1 1V20c0 .6-.4 1-1 1A17 17 0 0 1 3 4c0-.6.4-1 1-1h3.5c.6 0 1 .4 1 1 0 1.3.2 2.5.6 3.6.1.3 0 .7-.2 1z"/></svg>
        </span>
        <div><small>CALL US</small><strong>5550 123 400</strong></div>
      </div>
      <a class="btn">Schedule an Appointment</a>
    </div>
  </div>
</header>

<nav class="main-nav">
  <ul>
    <li class="active">Home</li>
    <li>About Us</li>
    <li>What to Expect</li>
    <li>Schedule an Appointment</li>
    <li>Testimonial</li>
    <li>Blog</li>
    <li>Contact Us</li>
  </ul>
</nav>

<section class="hero">
  <div class="ph" role="img" aria-label="Hero photo: smiling female doctor in white coat with stethoscope in a bright clinic corridor"></div>
  <div class="hero-text">
    <h1>WELLNESS CLINIC</h1>
    <p>We want to help our clients have a healthy, active lifestyle</p>
    <a class="btn">What to Expect</a>
  </div>
  <svg class="arrow l" width="16" height="28" viewBox="0 0 16 28"><path d="M14 2L3 14l11 12" stroke="#fff" stroke-width="3" fill="none"/></svg>
  <svg class="arrow r" width="16" height="28" viewBox="0 0 16 28"><path d="M2 2l11 12L2 26" stroke="#fff" stroke-width="3" fill="none"/></svg>
  <div class="dots"><i></i><i></i><i></i></div>
</section>

<section class="about">
  <div class="wrap">
    <div class="about-photo" role="img" aria-label="Photo: doctor with a smiling family of patients"></div>
    <div class="about-body">
      <h2 class="section-title"><span class="g">About</span> <span class="b">Willowmere Health Clinic</span></h2>
      <p>Our clinic is a friendly place for whole-family care. We focus on prevention, clear advice and treatment plans that fit your daily life. Every visit starts with listening, so we can understand your goals and help you reach them. Our team of doctors, nurses and therapists works together to support your health at every stage, from a first check-up to long-term care. We keep waiting times short, explain every step, and follow up after your visit so that you always know what comes next on your path to a healthy, active lifestyle.</p>
      <a class="btn">Read More</a>
    </div>
  </div>
</section>

<section class="services">
  <div class="wrap">
    <h2 class="section-title">What We Do</h2>
    <div class="rule"></div>
    <div class="cards">
      <div class="card">
        <div class="card-icon"><svg width="34" height="34" viewBox="0 0 24 24"><path fill="#fff" d="M10 3h4v7h7v4h-7v7h-4v-7H3v-4h7z"/></svg></div>
        <h3>Neurological Chiropractic</h3>
        <p>Gentle care for the spine and nerves to ease pain and restore natural movement.</p>
        <a class="btn btn-dark">Read More</a>
      </div>
      <div class="card">
        <div class="card-icon"><svg width="36" height="36" viewBox="0 0 24 24"><path fill="none" stroke="#fff" stroke-width="2" d="M1 12s4-7 11-7 11 7 11 7-4 7-11 7S1 12 1 12z"/><circle cx="12" cy="12" r="3" fill="#fff"/></svg></div>
        <h3>Eye Care And Surgery</h3>
        <p>Full eye exams, vision tests and modern surgical care for clear, healthy sight.</p>
        <a class="btn btn-dark">Read More</a>
      </div>
      <div class="card">
        <div class="card-icon"><svg width="34" height="34" viewBox="0 0 24 24"><path fill="#fff" d="M12 2s7 8 7 13a7 7 0 0 1-14 0c0-5 7-13 7-13z"/></svg></div>
        <h3>Diabetes Treatment</h3>
        <p>Ongoing support, tests and diet plans to help you manage blood sugar well.</p>
        <a class="btn btn-dark">Read More</a>
      </div>
      <div class="card">
        <div class="card-icon"><svg width="34" height="34" viewBox="0 0 24 24"><path fill="#fff" d="M12 21l-8.5-8.3A5 5 0 0 1 12 5.6a5 5 0 0 1 8.5 7.1z"/></svg></div>
        <h3>About Kids and Pregnancy</h3>
        <p>Caring checkups for mothers to be, newborns and growing children of all ages.</p>
        <a class="btn btn-dark">Read More</a>
      </div>
    </div>
    <a class="btn btn-white view">View All</a>
  </div>
</section>

<section class="expect">
  <div class="wrap">
    <div class="faq">
      <h2 class="section-title"><span class="g">What</span> <span class="b">to Expect</span></h2>
      <h4>What happens on my first visit?</h4>
      <p>We review your history, talk about your goals and run a short exam before any plan is made.</p>
      <h4>How long does a visit take?</h4>
      <p>Most first visits last about one hour; follow-ups are shorter.</p>
      <h4>Do I need a referral?</h4>
      <p>No referral is needed; simply call or book online.</p>
      <a class="btn">Read More</a>
    </div>
    <div class="expect-photo" role="img" aria-label="Photo: male doctor in white coat holding a clipboard"></div>
    <div class="hours">
      <h3>Opening Hours</h3>
      <table>
        <tr><td>Monday - Friday</td><td>08:00 - 20:00</td></tr>
        <tr><td>Saturday</td><td>09:00 - 17:00</td></tr>
        <tr><td>Sunday</td><td>09:00 - 12:00</td></tr>
      </table>
      <div class="emergency">
        <small>Emergency Line</small>
        <strong>1-800-555-0142</strong>
        <p>Call our team anytime in urgent cases outside opening hours.</p>
      </div>
    </div>
  </div>
</section>

<section class="testimonial">
  <h2 class="section-title">Testimonial</h2>
  <div class="avatar" role="img" aria-label="Portrait photo of a patient"></div>
  <blockquote>"From the first call to my last visit, the team made me feel welcome and heard. They explained every step, answered all my questions and helped me get back to running without pain. I recommend this clinic to anyone who wants real care and a clear plan."</blockquote>
  <cite><b>Daniel Hart</b> &nbsp;–&nbsp; Patient</cite>
  <svg class="arrow l" width="16" height="28" viewBox="0 0 16 28"><path d="M14 2L3 14l11 12" stroke="#fff" stroke-width="3" fill="none"/></svg>
  <svg class="arrow r" width="16" height="28" viewBox="0 0 16 28"><path d="M2 2l11 12L2 26" stroke="#fff" stroke-width="3" fill="none"/></svg>
</section>

<section class="blog">
  <div class="wrap">
    <h2 class="section-title">Recent Blog</h2>
    <div class="posts">
      <article class="post">
        <div class="post-photo p1 ph" role="img" aria-label="Blog photo: patient having an eye examination"></div>
        <div class="date"><b>24</b>NOV</div>
        <div class="post-caption"><h4>Simple steps to protect your eyes</h4><p>Easy daily habits that keep your vision sharp and healthy.</p></div>
        <a class="more">Read More</a>
      </article>
      <article class="post">
        <div class="post-photo p2 ph" role="img" aria-label="Blog photo: young child at a pediatric checkup"></div>
        <div class="date"><b>18</b>NOV</div>
        <div class="post-caption"><h4>Getting kids ready for checkups</h4><p>How to make doctor visits calm and fun for little ones.</p></div>
        <a class="more">Read More</a>
      </article>
      <article class="post">
        <div class="post-photo p3 ph" role="img" aria-label="Blog photo: doctor talking with a patient at a desk"></div>
        <div class="date"><b>10</b>NOV</div>
        <div class="post-caption"><h4>Living well with diabetes today</h4><p>Food, movement and care tips for balanced blood sugar.</p></div>
        <a class="more">Read More</a>
      </article>
    </div>
    <a class="btn view">View All</a>
  </div>
</section>

<footer class="site-footer">
  <div class="wrap">
    <div class="foot-brand">
      <div class="brand"><span class="b1">Willowmere</span><span class="b2">Health Clinic</span></div>
      <p>Caring for families with friendly, modern medicine.<br>© 2017 – All Rights Reserved</p>
    </div>
    <div class="foot-col">
      <h5>Quick Links</h5>
      <ul><li>Home</li><li>About Us</li><li>What to Expect</li><li>Testimonial</li><li>Blog</li><li>Contact Us</li></ul>
    </div>
    <div class="foot-col">
      <h5>Services</h5>
      <ul><li>Neurological Chiropractic</li><li>Eye Care and Surgery</li><li>Diabetes Treatment</li><li>About Kids and Pregnancy</li><li>General Checkups</li><li>Wellness Plans</li></ul>
    </div>
    <div class="foot-contact">
      <h5 class="foot-col" style="width:auto;font-size:14px;font-weight:700;text-transform:uppercase;margin-bottom:10px">Contact Info</h5>
      <ul>
        <li><b>Address:</b>48 Linden Row, Suite 2, Brookfield</li>
        <li><b>Phone:</b>5550 123 400</li>
        <li><b>Fax:</b>5550 123 401</li>
        <li><b>Email:</b>hello@willowmereclinic.example</li>
      </ul>
      <a class="btn">Schedule an Appointment</a>
    </div>
  </div>
</footer>

</body>
</html>
```